Corporate Business Card

Very professional, Modern, Not to busy, include phone address email, website
(253) 617-4930, 18761 52nd Avenue S, Kent, WA 98047, martin@plumlinegroup.com, varkoworks.com

Target Market(s)

Manufacturing

Industry/Entity Type

Aero, machining, manufacturing, Off road racing

Contact Information for Business Card

Phone, address email, website

```html
<!DOCTYPE html>
<html lang="en">
<head>
<meta charset="utf-8">
<title>Varko Works – Business Card</title>
<link href="https://fonts.googleapis.com/css2?family=Titillium+Web:wght@400;700&display=swap" rel="stylesheet">
<style>
  :root{
    --stage:#1c1c1c;
    --brand-red:#d1242c;
    --brand-navy:#1b3770;
    --ink-grey:#4a4a4a;
    --paper:#ffffff;
  }
  *{margin:0;padding:0;box-sizing:border-box}
  html,body{width:1200px;height:1122px;overflow:hidden}
  body{background:var(--stage);font-family:"Titillium Web",sans-serif;position:relative}
  .card{position:absolute;left:220px;width:760px;height:434px;border-radius:28px;overflow:hidden}
  .card-front{top:97px;background:var(--brand-red)}
  .card-back{top:591px;background:var(--paper)}

  .front-wordmark{position:absolute;left:0;right:0;top:150px;text-align:center;color:var(--paper);font-weight:700;font-size:64px;letter-spacing:2px;line-height:1}
  .front-rule{position:absolute;left:190px;top:250px;width:260px;height:2px;background:var(--paper)}

  .back-wordmark{position:absolute;right:60px;top:52px;color:var(--brand-navy);font-weight:700;font-size:38px;letter-spacing:1px;line-height:1}
  .back-logo-rule{position:absolute;right:200px;top:112px;width:200px;height:2px;background:var(--brand-navy)}

  .holder{position:absolute;left:60px;top:222px}
  .holder-name{color:var(--brand-navy);font-weight:700;font-size:30px;line-height:1;letter-spacing:.5px}
  .holder-title{color:var(--brand-red);font-weight:400;font-size:20px;line-height:1.3}
  .divider{position:absolute;left:250px;top:270px;width:460px;height:2px;background:var(--brand-navy)}
  .address{position:absolute;right:60px;top:284px;text-align:right;color:var(--ink-grey);font-size:16px;line-height:1.35}
  .name-rule{position:absolute;left:60px;top:290px;width:180px;height:2px;background:var(--brand-navy)}
  .contacts{position:absolute;left:60px;top:300px;list-style:none;color:var(--ink-grey);font-size:17px;line-height:1.55}
  .contacts li{display:flex;align-items:center;gap:10px}
  .contacts svg{width:15px;height:15px;fill:var(--brand-navy)}
  .footer-bands{position:absolute;left:0;bottom:0;width:760px;height:70px}
  .website{position:absolute;right:50px;bottom:14px;color:var(--paper);font-size:16px;letter-spacing:3px}
</style>
</head>
<body>
  <section class="card card-front" aria-label="Card front">
    <div class="front-wordmark">VARKO WORKS</div>
    <div class="front-rule"></div>
  </section>

  <section class="card card-back" aria-label="Card back">
    <div class="back-wordmark">VARKO WORKS</div>
    <div class="back-logo-rule"></div>

    <div class="holder">
      <div class="holder-name">DANIEL CRANE</div>
      <div class="holder-title">Managing Director</div>
    </div>
    <div class="divider"></div>
    <div class="address">18761 52nd Avenue S<br>Kent, WA 98047</div>
    <div class="name-rule"></div>

    <ul class="contacts">
      <li><svg viewBox="0 0 24 24" aria-hidden="true"><path d="M6.6 10.8a15.1 15.1 0 0 0 6.6 6.6l2.2-2.2a1 1 0 0 1 1-.25 11.4 11.4 0 0 0 3.6.57 1 1 0 0 1 1 1V20a1 1 0 0 1-1 1A17 17 0 0 1 3 4a1 1 0 0 1 1-1h3.5a1 1 0 0 1 1 1c0 1.25.2 2.45.57 3.57a1 1 0 0 1-.25 1z"/></svg>(253) 617-4930</li>
      <li><svg viewBox="0 0 24 24" aria-hidden="true"><path d="M2 5h20v14H2z M2 5l10 8 10-8" fill="none" stroke="#1b3770" stroke-width="2"/></svg>martin@plumlinegroup.com</li>
    </ul>

    <svg class="footer-bands" viewBox="0 0 760 70" preserveAspectRatio="none" aria-hidden="true">
      <polygon points="0,42 462,42 456,56 0,56" fill="#d1242c"/>
      <polygon points="0,60 470,60 490,22 760,22 760,70 0,70" fill="#1b3770"/>
    </svg>
    <div class="website">www.VarkoWorks.com</div>
  </section>
</body>
</html>
```